Brellwick Partners, LLC Stationary

Brellwick Partners, LLC is a new financial planning and consulting company. We are looking for designs on business cards, letterhead, envelopes, and anything else that would be useful. Our preference for business card design is two sided. We are looking for a professional and clean look with incorporating the logo and patriotic feel. Thank you to all who participate and good luck!

```html
<!DOCTYPE html>
<html lang="en">
<head>
<meta charset="utf-8">
<title>Brellwick Partners, LLC – Business Card</title>
<link rel="stylesheet" href="https://fonts.googleapis.com/css2?family=Arimo:wght@400;700&family=Cousine&display=swap">
<style>
  :root {
    --navy: #133a6b;
    --navy-deep: #0c2a52;
    --red: #cc3a3f;
    --ink: #3d3d3d;
    --paper: #ffffff;
    --stage: #e9e7e3;
    --muted-white: #dfe6ef;
  }
  * { box-sizing: border-box; margin: 0; padding: 0; }
  html, body {
    width: 1200px; height: 950px; overflow: hidden;
    background: var(--stage);
    font-family: "Arimo", Arial, sans-serif;
  }
  .sheet {
    position: relative; width: 1200px; height: 950px;
  }
  .card {
    position: absolute; left: 270px; width: 660px; height: 377px;
    border-radius: 4px; overflow: hidden;
    box-shadow: 0 10px 30px rgba(0,0,0,.18);
  }

  /* Back side */
  .card-back {
    top: 70px;
    background: linear-gradient(135deg, var(--navy) 0%, var(--navy-deep) 100%);
    color: var(--paper);
    display: flex; flex-direction: column; align-items: center; justify-content: center;
  }
  .card-back .brand-name { color: var(--paper); }
  .card-back .tagline { color: var(--muted-white); }
  .card-back .web {
    margin-top: 34px; font-family: "Cousine", monospace; font-size: 18px;
    letter-spacing: 4px; color: var(--muted-white);
  }

  /* Shared logo lockup */
  .brand { display: flex; flex-direction: column; align-items: center; }
  .brand-row { display: flex; align-items: center; gap: 12px; }
  .brand-mark { width: 22px; height: 22px; background: var(--red); }
  .brand-name {
    font-family: "Arimo", Arial, sans-serif; font-weight: 700;
    font-size: 30px; letter-spacing: 2px; color: var(--navy);
    text-transform: uppercase;
  }
  .tagline {
    margin-top: 6px; font-size: 10px; letter-spacing: 2.6px;
    text-transform: uppercase; color: var(--red);
    border-top: 1px solid currentColor; padding-top: 4px;
  }

  /* Front side */
  .card-front { top: 503px; background: var(--paper); }
  .card-front .brand { position: absolute; top: 38px; left: 150px; }
  .band {
    position: absolute; top: 150px; left: 0; width: 100%; height: 56px;
    display: flex;
  }
  .band-blue {
    flex: 0 0 72%; background: var(--navy);
    display: flex; flex-direction: column; justify-content: center; align-items: flex-end;
    padding-right: 34px; color: var(--paper);
  }
  .band-red { flex: 1; background: var(--red); position: relative; }
  .band-red .dot {
    position: absolute; left: -14px; top: 14px; width: 28px; height: 28px;
    border-radius: 50%; background: var(--paper);
  }
  .holder-name { font-weight: 700; font-size: 19px; letter-spacing: 1px; }
  .holder-title { font-size: 14px; letter-spacing: 1px; }

  .contact {
    position: absolute; left: 32px; top: 230px; list-style: none;
    font-size: 16px; color: var(--ink); line-height: 1.45;
  }
  .contact li { display: flex; align-items: center; gap: 10px; }
  .contact svg { width: 16px; height: 16px; fill: var(--navy); flex: none; }

  .address {
    position: absolute; right: 34px; bottom: 34px; text-align: right;
    font-family: "Cousine", monospace; font-size: 16px; color: #6a6a6a;
    line-height: 1.5; font-style: normal;
  }
  .address .web { letter-spacing: 3px; }
</style>
</head>
<body>
<main class="sheet">

  <section class="card card-back" aria-label="Card back">
    <div class="brand">
      <div class="brand-row">
        <span class="brand-mark"></span>
        <span class="brand-name">Brellwick Partners, LLC</span>
      </div>
      <span class="tagline">Financial Planning and Consulting</span>
    </div>
    <p class="web">www.brellwick.com</p>
  </section>

  <section class="card card-front" aria-label="Card front">
    <div class="brand">
      <div class="brand-row">
        <span class="brand-mark"></span>
        <span class="brand-name">Brellwick Partners, LLC</span>
      </div>
      <span class="tagline">Financial Planning and Consulting</span>
    </div>

    <div class="band">
      <div class="band-blue">
        <span class="holder-name">MARCUS HALE</span>
        <span class="holder-title">PRESIDENT</span>
      </div>
      <div class="band-red"><span class="dot"></span></div>
    </div>

    <ul class="contact">
      <li>
        <svg viewBox="0 0 24 24" aria-hidden="true"><path d="M6.6 10.8a15 15 0 0 0 6.6 6.6l2.2-2.2a1 1 0 0 1 1-.25 11.4 11.4 0 0 0 3.6.57 1 1 0 0 1 1 1V20a1 1 0 0 1-1 1A17 17 0 0 1 3 4a1 1 0 0 1 1-1h3.5a1 1 0 0 1 1 1c0 1.25.2 2.45.57 3.57a1 1 0 0 1-.25 1z"/></svg>
        555 0142 2281
      </li>
      <li>
        <svg viewBox="0 0 24 24" aria-hidden="true"><path d="M6 3h12v5H6zM4 9h16a2 2 0 0 1 2 2v6h-4v4H6v-4H2v-6a2 2 0 0 1 2-2zm4 7v3h8v-3z"/></svg>
        555 0187 3342
      </li>
      <li>
        <svg viewBox="0 0 24 24" aria-hidden="true"><path d="M2 5h20v14H2zm2 2v.5l8 5 8-5V7zm0 2.9V17h16V9.9l-8 5z"/></svg>
        marcus@brellwick.com
      </li>
    </ul>

    <address class="address">
      2710 Harlow Lane<br>
      Linden Ridge, NY 10420<br>
      <span class="web">www.brellwick.com</span>
    </address>
  </section>

</main>
</body>
</html>
```